Venture 482 - Lumora Book Cover

I am looking for a Lumora book cover for my book about "Venture 482".
The Book is Titled:
Venture 482 Ascended
Shaping Outcomes: Paths To Unlocking Cosmic Truths
Author is Dorian Pell
Here is a book description that may help you understand more about it:
Inspired by the genius of Edwin Marlowe, this comprehensive guide delves into the ancient wisdom and cutting-edge science behind the 482 method, a powerful tool for manifesting your desires. Whether you're seeking personal growth, financial success, or spiritual enlightenment, this book provides advanced techniques and methods to transform your dreams into reality.
Any questions please ask.
Thanks
Owen

```html
<!DOCTYPE html>
<html lang="en">
<head>
<meta charset="utf-8">
<title>Venture 482 Ascended — Shaping Outcomes</title>
<link rel="stylesheet" href="https://fonts.googleapis.com/css2?family=Oswald:wght@300;400;500&family=Pinyon+Script&display=swap">
<style>
  :root {
    --mat: #ebebeb;
    --space: #050304;
    --ember: #8e1506;
    --flame: #c8560c;
    --gold: #e0a21c;
    --haze: #efe2c4;
    --ink: #0c0a08;
    --paper: #ffffff;
  }
  * { margin: 0; padding: 0; box-sizing: border-box; }
  html, body {
    width: 1200px;
    height: 1200px;
    overflow: hidden;
    background: var(--mat);
  }
  .cover {
    position: absolute;
    left: 219px;
    top: 29px;
    width: 761px;
    height: 1142px;
    overflow: hidden;
    background:
      radial-gradient(ellipse 70% 45% at 15% 95%, var(--ember) 0%, transparent 70%),
      radial-gradient(ellipse 70% 50% at 95% 85%, var(--gold) 0%, transparent 75%),
      linear-gradient(180deg, var(--space) 0%, var(--space) 32%, #2a0b06 48%, var(--flame) 75%, #d88a18 100%);
  }
  .cover__artwork {
    position: absolute;
    left: 43px;
    top: 258px;
    width: 676px;
    height: 676px;
    border-radius: 50%;
    background: radial-gradient(circle at 50% 50%, var(--haze) 0%, rgba(225, 200, 150, 0.75) 35%, rgba(190, 140, 90, 0.35) 62%, transparent 72%);
  }
  .cover__series {
    position: absolute;
    top: 112px;
    width: 100%;
    text-align: center;
    font-family: "Oswald", sans-serif;
    font-weight: 400;
    font-size: 36px;
    letter-spacing: 8px;
    color: var(--paper);
    text-transform: uppercase;
  }
  .cover__series em { font-style: italic; }
  .cover__title {
    position: absolute;
    top: 134px;
    width: 100%;
    text-align: center;
    font-family: "Oswald", sans-serif;
    font-weight: 400;
    font-size: 180px;
    line-height: 1;
    letter-spacing: 2px;
    color: var(--paper);
    text-transform: uppercase;
  }
  .cover__title-script {
    position: absolute;
    top: 300px;
    width: 100%;
    text-align: center;
    font-family: "Pinyon Script", cursive;
    font-size: 150px;
    line-height: 1;
    color: var(--paper);
  }
  .cover__subtitle {
    position: absolute;
    top: 990px;
    width: 100%;
    text-align: center;
    font-family: "Oswald", sans-serif;
    font-weight: 400;
    font-size: 44px;
    color: var(--paper);
  }
  .cover__author {
    position: absolute;
    top: 1068px;
    width: 100%;
    text-align: center;
    font-family: "Oswald", sans-serif;
    font-weight: 400;
    font-size: 44px;
    letter-spacing: 10px;
    color: var(--ink);
    text-transform: uppercase;
  }
</style>
</head>
<body>
  <main class="cover">
    <div class="cover__artwork" role="img" aria-label="Glowing sacred geometry star diagram over a cosmic nebula"></div>
    <p class="cover__series">Venture <em>482</em> Ascended</p>
    <h1 class="cover__title">Shaping</h1>
    <p class="cover__title-script">Outcomes</p>
    <p class="cover__subtitle">Paths To Unlocking Cosmic Truths</p>
    <p class="cover__author">Dorian Pell</p>
  </main>
</body>
</html>
```